Roofing Contractor business card redesign

I want to redesign my business card with a fresh, eye catching concept

Target Market(s)

Residential Roofing Clients, potential employees, and subcontractors.

Industry/Entity Type

Business

Colors

Designer to choose colors to be used in the design.

Requirements
Nice to have
• I just want something that's more pleasing to the eye. You can use a combination of either / or of my logos.

```html
<!DOCTYPE html>
<html lang="en">
<head>
<meta charset="utf-8">
<title>Steady Crew Builders – Business Card</title>
<link href="https://fonts.googleapis.com/css2?family=Roboto+Condensed:wght@400;700&display=swap" rel="stylesheet">
<style>
  :root {
    --backdrop: #e9e4dd;
    --card-white: #f7f6f4;
    --brown: #40120f;
    --orange: #e86f22;
    --text-dark: #3a2a28;
    --text-mid: #5a4a47;
    --divider: #d8d3ce;
  }
  * { margin: 0; padding: 0; box-sizing: border-box; }
  html, body { width: 1200px; height: 911px; overflow: hidden; }
  body {
    background: var(--backdrop);
    font-family: "Roboto Condensed", Arial, sans-serif;
    position: relative;
  }
  .card {
    position: absolute;
    width: 560px;
    height: 320px;
    border-radius: 18px;
    overflow: hidden;
    box-shadow: 0 10px 28px rgba(0,0,0,.18);
  }

  /* Front */
  .card-front { left: 70px; top: 110px; background: var(--card-white); }
  .brand {
    position: absolute; left: 40px; top: 100px; width: 230px;
    display: flex; flex-direction: column; align-items: center; gap: 10px;
  }
  .brand-row { display: flex; align-items: center; gap: 10px; }
  .brand-dot { width: 34px; height: 34px; border-radius: 50%; background: var(--orange); }
  .brand-name {
    font-weight: 700; font-size: 38px; color: var(--brown);
    letter-spacing: -0.5px; line-height: 1;
  }
  .brand-sub { font-weight: 700; font-size: 19px; color: var(--brown); }
  .divider {
    position: absolute; left: 300px; top: 40px; width: 1px; height: 190px;
    background: var(--divider);
  }
  .contact { position: absolute; left: 322px; top: 40px; width: 225px; }
  .person-name { font-weight: 700; font-size: 20px; color: var(--brown); }
  .person-role { font-size: 15px; color: var(--orange); line-height: 1.25; margin-top: 2px; }
  .address { font-size: 13.5px; color: var(--text-mid); line-height: 1.35; margin-top: 10px; }
  .contact-list { list-style: none; margin-top: 8px; font-size: 13.5px; color: var(--text-mid); }
  .contact-list li { display: flex; align-items: center; gap: 7px; line-height: 1.45; }
  .contact-list svg { width: 12px; height: 12px; fill: var(--brown); flex: none; }

  .band-brown {
    position: absolute; left: 0; bottom: 0; width: 410px; height: 44px;
    background: var(--brown);
    display: flex; align-items: center; justify-content: center;
  }
  .band-orange {
    position: absolute; right: 0; bottom: 26px; width: 150px; height: 18px;
    background: var(--orange);
  }
  .band-orange-base {
    position: absolute; right: 0; bottom: 0; width: 150px; height: 26px;
    background: var(--card-white);
  }
  .band-badge {
    position: absolute; left: 386px; bottom: 6px; width: 52px; height: 52px;
    border-radius: 50%; background: var(--brown); border: 3px solid var(--card-white);
  }
  .web { font-size: 15px; letter-spacing: 5px; color: #f2e9e6; }

  /* Back */
  .card-back {
    left: 570px; top: 480px; background: var(--brown);
  }
  .back-web {
    position: absolute; left: 28px; top: 50%;
    transform: translate(-50%, -50%) rotate(90deg) translateY(-50%);
    transform-origin: center;
  }
  .back-web-wrap {
    position: absolute; left: 40px; top: 0; height: 100%; width: 20px;
    display: flex; align-items: center; justify-content: center;
  }
  .back-web-wrap .web { transform: rotate(90deg); white-space: nowrap; }
  .back-art {
    position: absolute; left: 50%; top: 50%; width: 150px; height: 150px;
    transform: translate(-50%, -50%);
  }
</style>
</head>
<body>

<section class="card card-front">
  <div class="brand">
    <div class="brand-row">
      <span class="brand-name">Steady Crew</span>
      <span class="brand-dot"></span>
    </div>
    <span class="brand-sub">Builders, Inc.</span>
  </div>

  <div class="divider"></div>

  <div class="contact">
    <p class="person-name">DALE HARMON</p>
    <p class="person-role">Summit Certified Roof Inspector<br>Licensed Property Adjuster</p>
    <p class="address">4410 Ridgeview Lane Suite 118<br>Plano, TX 75024</p>
    <ul class="contact-list">
      <li><svg viewBox="0 0 12 12"><path d="M2 0h3l1 3-2 1.5a7 7 0 0 0 3.5 3.5L9 6l3 1v3a2 2 0 0 1-2 2A10 10 0 0 1 0 2a2 2 0 0 1 2-2z"/></svg>(555) 214-7730</li>
      <li><svg viewBox="0 0 12 12"><path d="M3 0h6v4H3zM1 4h10v6H9v2H3v-2H1zM4 8v3h4V8z"/></svg>(555) 318-6402</li>
      <li><svg viewBox="0 0 12 12"><path d="M0 2h12v8H0zM1 3l5 4 5-4v-.2H1z" fill-rule="evenodd"/></svg>dale@steadycrewtx.com</li>
    </ul>
  </div>

  <div class="band-brown"><span class="web">www.steadycrewtx.com</span></div>
  <div class="band-orange-base"></div>
  <div class="band-orange"></div>
  <div class="band-badge"></div>
</section>

<section class="card card-back">
  <div class="back-web-wrap"><span class="web">www.steadycrewtx.com</span></div>
  <svg class="back-art" viewBox="0 0 150 150" role="img" aria-label="Circular illustration of a roofing crew at work">
    <defs>
      <radialGradient id="crewTone" cx="50%" cy="45%" r="60%">
        <stop offset="0%" stop-color="#f4c64a"/>
        <stop offset="55%" stop-color="#e86f22"/>
        <stop offset="100%" stop-color="#6b2a1c"/>
      </radialGradient>
    </defs>
    <circle cx="75" cy="75" r="72" fill="#f7f6f4"/>
    <circle cx="75" cy="75" r="66" fill="url(#crewTone)"/>
  </svg>
</section>

</body>
</html>
```